Request for Business Card Design

Hi. My name is Marlene, I am looking for a new business card design for my company, Quarrow Signal Instruments, LLC. I really like the design you did for Tarsel Venture and was hoping you could do something similar using our full logo and our mark. I am also open to any raised texture design using our mark. I have attached our full logo, which would need to be somewhere on the card, as well as the mark in both outline and full form, as well as our brand colors / guide. The card does not have to be white, as long as our logo and mark appear. I actually like darker colored business cards more, but am open to all options. If you are interested in working with me, please let me know. We would also take the business card design into letterhead design if you can do that.

```html
<!DOCTYPE html>
<html lang="en">
<head>
<meta charset="utf-8">
<title>Quarrow Signal Instruments – Business Card</title>
<link rel="stylesheet" href="https://fonts.googleapis.com/css2?family=Open+Sans:wght@400;600;700&display=swap">
<style>
  :root {
    --stage: #222223;
    --card-dark: #3e3f41;
    --brand-blue: #1899c9;
    --brand-blue-deep: #0f7fa8;
    --brand-blue-light: #4fb6dc;
    --text-light: #ffffff;
    --text-soft: #e6e8ea;
  }
  * { box-sizing: border-box; margin: 0; padding: 0; }
  html, body {
    width: 1200px; height: 780px; overflow: hidden;
    background: var(--stage);
    font-family: "Open Sans", Arial, sans-serif;
  }
  .canvas { position: relative; width: 1200px; height: 780px; }

  .card {
    position: absolute;
    width: 600px; height: 343px;
    border-radius: 22px;
    overflow: hidden;
  }

  /* Back of card */
  .card--back {
    left: 70px; top: 40px;
    background: var(--brand-blue);
  }
  .card--back .pattern-area {
    position: absolute; inset: 0;
    background: linear-gradient(160deg, var(--brand-blue-light) 0%, var(--brand-blue) 45%, var(--brand-blue-deep) 100%);
  }
  .card--back .back-brand {
    position: absolute; right: 30px; bottom: 26px;
    display: flex; align-items: center; gap: 8px;
    color: var(--text-light);
    font-weight: 700; font-size: 13px; letter-spacing: 0.5px;
  }
  .brand-dot {
    width: 14px; height: 14px; border-radius: 50%;
    background: var(--text-light);
  }

  /* Front of card */
  .card--front {
    left: 530px; top: 410px;
    background: var(--card-dark);
    border-bottom: 5px solid var(--brand-blue);
    border-left: 3px solid var(--brand-blue);
  }
  .front-brand {
    position: absolute; left: 30px; top: 34px;
    display: flex; align-items: center; gap: 14px;
  }
  .front-brand .brand-dot {
    width: 40px; height: 40px; background: var(--brand-blue);
  }
  .front-brand .brand-name {
    color: var(--text-light);
    font-weight: 700; font-size: 21px; letter-spacing: 1px;
    text-transform: uppercase; line-height: 1.1;
  }

  .person {
    position: absolute; right: 0; top: 92px;
    display: flex; align-items: stretch;
  }
  .person-text { text-align: right; padding-right: 12px; }
  .person-name {
    color: var(--brand-blue);
    font-weight: 700; font-size: 34px; line-height: 1;
  }
  .person-role {
    color: var(--text-light);
    font-size: 15px; margin-top: 4px;
  }
  .person-bar { width: 16px; background: var(--brand-blue); }

  .address {
    position: absolute; left: 92px; top: 170px;
    color: var(--text-soft);
    font-size: 14px; line-height: 1.4;
  }

  .contacts {
    position: absolute; left: 92px; top: 230px;
    list-style: none;
    color: var(--text-soft);
    font-size: 13px; line-height: 1;
  }
  .contacts li {
    display: flex; align-items: center; gap: 9px;
    height: 19px;
  }
  .contacts svg { width: 13px; height: 13px; flex: none; }
</style>
</head>
<body>
<main class="canvas">

  <section class="card card--back" aria-label="Card back">
    <div class="pattern-area" role="img" aria-label="Repeating pattern of the company mark across the card"></div>
    <div class="back-brand"><span class="brand-dot"></span>QUARROW SIGNAL INSTRUMENTS</div>
  </section>

  <section class="card card--front" aria-label="Card front">
    <div class="front-brand">
      <span class="brand-dot"></span>
      <span class="brand-name">Quarrow Signal<br>Instruments</span>
    </div>

    <div class="person">
      <div class="person-text">
        <div class="person-name">Marlene</div>
        <div class="person-role">Director</div>
      </div>
      <div class="person-bar"></div>
    </div>

    <address class="address" style="font-style:normal">
      1180 Harlow Ridge Road •<br>
      Belmont Falls, CO 80999
    </address>

    <ul class="contacts">
      <li>
        <svg viewBox="0 0 24 24" fill="var(--brand-blue)" aria-hidden="true"><path d="M6.6 10.8a15 15 0 0 0 6.6 6.6l2.2-2.2a1 1 0 0 1 1-.25 11.4 11.4 0 0 0 3.6.57 1 1 0 0 1 1 1V20a1 1 0 0 1-1 1A17 17 0 0 1 3 4a1 1 0 0 1 1-1h3.5a1 1 0 0 1 1 1c0 1.25.2 2.45.57 3.6a1 1 0 0 1-.25 1z"/></svg>
        +001 555 210 4830
      </li>
      <li>
        <svg viewBox="0 0 24 24" fill="var(--brand-blue)" aria-hidden="true"><rect x="3" y="8" width="18" height="12" rx="2"/><rect x="7" y="3" width="10" height="6" fill="var(--text-soft)"/><rect x="7" y="12" width="10" height="2" fill="var(--card-dark)"/></svg>
        +001 555 210 4831
      </li>
      <li>
        <svg viewBox="0 0 24 24" fill="none" stroke="var(--brand-blue)" stroke-width="2" aria-hidden="true"><circle cx="12" cy="12" r="9"/><path d="M3 12h18M12 3c3 3 3 15 0 18M12 3c-3 3-3 15 0 18"/></svg>
        www.quarrowsignal.com
      </li>
      <li>
        <svg viewBox="0 0 24 24" fill="none" stroke="var(--brand-blue)" stroke-width="2" aria-hidden="true"><rect x="3" y="6" width="18" height="13" rx="1"/><path d="M3 7l9 7 9-7"/></svg>
        info@quarrowsignal.com
      </li>
    </ul>
  </section>

</main>
</body>
</html>
```